Upmarket Dessert Lounge needs a Business Card Design

We are an upmarket dessert lounge needing a business card to match our image.

We want something that is simple yet beautiful, feminine, classy, sophisticated and elegant. We want it to stand out and don't mind if it is bold.

The design should include our logo and colours of red or maroon with gold highlights. We don't mind if black is used.

Marlow & Quince

Target Market(s)

For those who like to indulge or treat themselves and give in to their temptations on good quality desserts.

Industry/Entity Type

Business

Requirements
Must have
• Must include our logo and our name

Marlow & Quince

M & Q

```html
<!DOCTYPE html>
<html lang="en">
<head>
<meta charset="utf-8">
<title>Marlow &amp; Quince — Business Card</title>
<link href="https://fonts.googleapis.com/css2?family=Tinos:wght@400;700&display=swap" rel="stylesheet">
<style>
  :root {
    --backdrop: #ece7e1;
    --card-front: #ffffff;
    --card-back: #fdd29b;
    --maroon: #7e1c1f;
    --ink: #4a4a4a;
    --rule: #8a8a8a;
  }
  * { box-sizing: border-box; margin: 0; padding: 0; }
  html, body { width: 1200px; height: 417px; overflow: hidden; }
  body {
    background: var(--backdrop);
    position: relative;
    font-family: "Tinos", "Times New Roman", serif;
  }
  .card {
    position: absolute;
    top: 61px;
    width: 515px;
    height: 292px;
    border-radius: 14px;
    box-shadow: 0 2px 6px rgba(0,0,0,0.25);
  }
  .card--front { left: 55px; background: var(--card-front); }
  .card--back { left: 630px; background: var(--card-back); }

  .brand-name {
    position: absolute;
    font-family: "Tinos", "Times New Roman", serif;
    font-weight: 400;
    font-size: 25px;
    letter-spacing: 0.5px;
    color: var(--maroon);
    text-transform: uppercase;
    white-space: nowrap;
    transform: translate(-50%, -50%);
  }
  .card--front .brand-name { left: 153px; top: 144px; }
  .card--back .brand-name { left: 258px; top: 144px; }

  .divider {
    position: absolute;
    left: 295px;
    top: 66px;
    width: 1.5px;
    height: 172px;
    background: linear-gradient(to bottom, transparent, var(--rule) 20%, var(--rule) 80%, transparent);
  }
  .contact {
    position: absolute;
    left: 315px;
    top: 68px;
    color: var(--ink);
  }
  .contact__name {
    font-weight: 700;
    font-size: 18px;
    color: var(--maroon);
    line-height: 22px;
  }
  .contact__title { font-size: 13px; line-height: 16px; margin-bottom: 13px; }
  .contact__list { list-style: none; }
  .contact__item {
    display: flex;
    align-items: center;
    gap: 6px;
    font-size: 13.5px;
    line-height: 20px;
  }
  .contact__icon { width: 10px; height: 10px; fill: var(--maroon); flex: none; }
  .contact__address { font-size: 13.5px; line-height: 19px; margin-top: 7px; padding-left: 2px; }

  .card__web {
    position: absolute;
    left: 0; right: 0;
    top: 258px;
    text-align: center;
    font-size: 12.5px;
    letter-spacing: 2.6px;
    color: var(--ink);
  }
</style>
</head>
<body>
  <section class="card card--front">
    <div class="brand-name">Marlow &amp; Quince</div>
    <div class="divider"></div>
    <div class="contact">
      <div class="contact__name">YOUR NAME</div>
      <div class="contact__title">Title</div>
      <ul class="contact__list">
        <li class="contact__item">
          <svg class="contact__icon" viewBox="0 0 10 10"><path d="M2 0.5 L3.6 2.8 L2.7 3.8 C3.3 5.2 4.8 6.7 6.2 7.3 L7.2 6.4 L9.5 8 L8.3 9.5 C4.5 9.3 0.7 5.5 0.5 1.7 Z"/></svg>
          +2348000451938
        </li>
        <li class="contact__item">
          <svg class="contact__icon" viewBox="0 0 10 10"><path d="M2.5 0 H7.5 V10 H2.5 Z M3.3 1 V7.5 H6.7 V1 Z M4.4 8.2 H5.6 V9.2 H4.4 Z"/></svg>
          +2348000451938
        </li>
        <li class="contact__item">
          <svg class="contact__icon" viewBox="0 0 10 10"><path d="M0 2 H10 V8 H0 Z" /><path d="M0 2 L5 5.5 L10 2" fill="none" stroke="#fff" stroke-width="0.8"/></svg>
          info@marlowquince.com
        </li>
        <li class="contact__item">
          <svg class="contact__icon" viewBox="0 0 10 10"><circle cx="5" cy="5" r="5"/><path d="M0.5 5 H9.5" stroke="#fff" stroke-width="0.9"/></svg>
          www.marlowquince.com
        </li>
      </ul>
      <div class="contact__address">00, Complex name<br>City, State 0025</div>
    </div>
  </section>

  <section class="card card--back">
    <div class="brand-name">Marlow &amp; Quince</div>
    <div class="card__web">www.marlowquince.com</div>
  </section>
</body>
</html>
```